Business Card Design Project

I require a business card with the following information on them for various different people;
name
m:
f:
e:
I have a logo already and will attached that. We are in the construction industry. I require something clean and simple but eye catching at the same time. You can use another colour with our logo if you like and you can style the logo as well if you wish. I am open.
Also it needs to be front and back design.
Industry/Entity Type
Construction
Requirements
Must have
- Logo, name, mobile, fax and email address.
Front and back design

```html
<!DOCTYPE html>
<html lang="en">
<head>
<meta charset="utf-8">
<title>Stonebridge Builders – Business Card, Front and Back</title>
<link href="https://fonts.googleapis.com/css2?family=Questrial&display=swap" rel="stylesheet">
<style>
  :root {
    --page: #1c1c1c;
    --card-top: #1a1a1a;
    --card-bottom: #050505;
    --green: #8cc63f;
    --green-bright: #a6e04a;
    --green-dark: #1f3a12;
    --silver-light: #e6e6e6;
    --silver-dark: #3a3a3a;
    --text-light: #e8e8e8;
    --rule: #4a4a4a;
  }
  * { margin: 0; padding: 0; box-sizing: border-box; }
  html, body { width: 1200px; height: 900px; overflow: hidden; }
  body {
    background: var(--page);
    font-family: "Questrial", "Century Gothic", sans-serif;
    position: relative;
  }
  .card {
    position: absolute;
    left: 250px;
    width: 700px;
    height: 400px;
    border-radius: 26px;
    overflow: hidden;
    background: linear-gradient(160deg, var(--card-top), var(--card-bottom) 70%);
    box-shadow: 0 10px 30px rgba(0,0,0,.6);
  }
  .card--front { top: 30px; }
  .card--back { top: 470px; }
  .card__bands { position: absolute; inset: 0; }

  .wordmark {
    position: absolute;
    display: flex;
    align-items: center;
    gap: 14px;
    color: var(--green);
    font-size: 34px;
    letter-spacing: 1px;
    white-space: nowrap;
  }
  .wordmark__square { width: 26px; height: 26px; background: var(--green); }
  .card--front .wordmark { top: 72px; left: 50%; transform: translateX(-50%); }
  .card--back .wordmark { top: 140px; left: 50%; transform: translateX(-50%); font-size: 42px; }
  .card--back .wordmark__square { width: 32px; height: 32px; }

  .front__rule {
    position: absolute; top: 150px; left: 130px; width: 440px; height: 1px;
    background: linear-gradient(90deg, transparent, var(--rule), transparent);
  }
  .holder-name {
    position: absolute; top: 196px; left: 50px;
    color: var(--green); font-size: 30px; letter-spacing: 1px;
  }
  .contact {
    position: absolute; top: 248px; left: 50px;
    display: grid; grid-template-columns: 220px 230px; row-gap: 10px;
    color: var(--text-light); font-size: 16px;
  }
  .contact__item { display: flex; align-items: center; gap: 9px; }
  .contact__icon { width: 18px; height: 18px; flex: none; }
</style>
</head>
<body>

<section class="card card--front" aria-label="Card front">
  <svg class="card__bands" viewBox="0 0 700 400" preserveAspectRatio="none">
    <polygon points="0,310 700,215 700,245 0,340" fill="var(--green-dark)"/>
    <polygon points="0,336 700,241 700,250 0,345" fill="var(--green)"/>
    <polygon points="0,345 700,250 700,290 0,385" fill="#0b0b0b"/>
    <polygon points="0,375 700,280 700,300 0,400" fill="var(--green-dark)"/>
    <polygon points="500,240 700,212 700,200 520,224" fill="#8a8a8a"/>
  </svg>
  <div class="wordmark"><span class="wordmark__square"></span>Stonebridge Builders</div>
  <div class="front__rule"></div>
  <h1 class="holder-name">MARTIN HALE</h1>
  <div class="contact">
    <div class="contact__item">
      <svg class="contact__icon" viewBox="0 0 18 18"><rect x="5" y="1" width="8" height="16" rx="2" fill="var(--green)"/><rect x="6.5" y="3.5" width="5" height="8" fill="#111"/></svg>
      xxxxxxxxxx
    </div>
    <div class="contact__item">
      <svg class="contact__icon" viewBox="0 0 18 18"><rect x="2" y="7" width="14" height="8" rx="1" fill="var(--green)"/><rect x="5" y="2" width="8" height="6" fill="var(--green)"/><rect x="5" y="10" width="8" height="1.5" fill="#111"/></svg>
      xxx xxx xxxx
    </div>
    <div class="contact__item">
      <svg class="contact__icon" viewBox="0 0 18 18"><rect x="1.5" y="4" width="15" height="10" fill="none" stroke="var(--green)" stroke-width="1.6"/><path d="M1.5 4 L9 10 L16.5 4" fill="none" stroke="var(--green)" stroke-width="1.6"/></svg>
      name@website.com
    </div>
    <div class="contact__item">
      <svg class="contact__icon" viewBox="0 0 18 18"><circle cx="9" cy="9" r="7.5" fill="none" stroke="var(--green)" stroke-width="1.6"/><ellipse cx="9" cy="9" rx="3" ry="7.5" fill="none" stroke="var(--green)" stroke-width="1.3"/><path d="M1.5 9 H16.5" stroke="var(--green)" stroke-width="1.3"/></svg>
      www.websitename.com
    </div>
  </div>
</section>

<section class="card card--back" aria-label="Card back">
  <svg class="card__bands" viewBox="0 0 700 400" preserveAspectRatio="none">
    <defs>
      <linearGradient id="silver" x1="0" x2="1" y1="0" y2="0">
        <stop offset="0" stop-color="var(--silver-dark)"/>
        <stop offset="0.6" stop-color="var(--silver-light)"/>
        <stop offset="1" stop-color="#7a7a7a"/>
      </linearGradient>
    </defs>
    <rect x="0" y="262" width="700" height="3" fill="var(--green-bright)"/>
    <rect x="0" y="272" width="700" height="60" fill="url(#silver)"/>
    <rect x="0" y="338" width="700" height="2" fill="var(--green)"/>
  </svg>
  <div class="wordmark"><span class="wordmark__square"></span>Stonebridge Builders</div>
</section>

</body>
</html>
```